Redesign Craft Brewing Recipe Website

Originally built with Bootstrap just to get the site going, I am seeking a complete redesign of the sites home page and recipe page. I am an experienced web developer with no graphic background, initially just looking for psd mocks.

I prefer styles that are clean and modern, and would prefer anything that is fun, engaging, and has an organic feel to it. I currently have a cartoon rabbit as a logo, but it needs some modification/tweaking, so any help in that area would be great as well.

Current site:
http://velvetfinch.cloudpagehost.net/

Current launch page/logo:
http://www.velvetfinch.com/

I like the overall layout of the elements currently, but the design sucks.

The launch page is at the following URL

Reason: Still looking for a more modern design. Designs received so far are too similar to the original.

My site is content based and does not contain images or products. Your design should not consist of large images.

Reason: The website has very little images, so the designs need to be more text and content based. The header needs to be very small and should not contain an ad rotater.

Target Market(s)

Home brewers, Craft brewers, Microbreweries, Brewpubs

Requirements
Must have
• Web 2.0 Look and Feel, Fun, Hip, Focus on content
Should not have
• A large photo as a header

```html
<!DOCTYPE html>
<html lang="en">
<head>
<meta charset="utf-8">
<title>Velvetfinch – Craft Beer Recipes</title>
<link rel="stylesheet" href="https://fonts.googleapis.com/css2?family=Nunito+Sans:ital,wght@0,400;0,600;0,700;1,800&family=Oswald:wght@500&display=swap">
<style>
:root{
  --cream:#f1ece6;
  --cream-dark:#e4ddd5;
  --wood:#3b3b3b;
  --wood-light:#4a4a4a;
  --wood-dark:#262626;
  --ink:#2e2e2e;
  --red:#c22a1e;
  --orange:#e07a00;
  --cyan:#0aa2d6;
  --author:#b87c5c;
  --srm-red:#b3321c;
  --srm-teal:#2a978a;
  --srm-green:#5a9f19;
  --srm-blue:#1b76b6;
  --stat-bg:#e9e9e9;
  --card-bg:#f1f1f1;
  --copyright:#a8542e;
  --join:#e88a1c;
  --social:#2f6fb3;
}
*{box-sizing:border-box;margin:0;padding:0}
html,body{width:919px;height:1200px;overflow:hidden}
body{position:relative;font-family:"Nunito Sans",Arial,sans-serif;color:var(--ink);
  background:linear-gradient(90deg,var(--wood) 0%,var(--wood-light) 20%,var(--wood) 40%,var(--wood-light) 60%,var(--wood) 80%,var(--wood-light) 100%)}
.site-header{position:absolute;left:0;top:0;width:919px;height:88px;background:var(--cream);border-bottom:3px solid var(--cream-dark)}
.brand{position:absolute;left:118px;top:29px;display:flex;align-items:center;gap:7px;font-size:22px;font-weight:700;color:var(--red);white-space:nowrap}
.brand-dot{width:18px;height:18px;border-radius:50%;background:var(--red)}
.search{position:absolute;left:495px;top:3px;width:153px;height:18px;background:#fff;border:1px solid #bbb;display:flex}
.search span{flex:1;font-size:10px;color:#888;padding:1px 4px}
.search b{width:17px;border-left:1px solid #bbb;display:flex;align-items:center;justify-content:center}
.top-links{position:absolute;left:662px;top:3px;display:flex;gap:20px;font-size:12px;color:var(--red);white-space:nowrap}
.tagline{position:absolute;left:304px;top:30px;font-size:11px;white-space:nowrap}
.share{position:absolute;left:672px;top:31px;display:flex;gap:4px}
.share span{height:13px;border:1px solid #b8c4d8;background:#eef2f8;font-size:8px;padding:0 4px;line-height:11px;color:#3b5590;white-space:nowrap}
.social-top{position:absolute;left:774px;top:31px;display:flex;gap:9px}
.social-top i{width:13px;height:14px;background:#b3aca5;border-radius:2px}
.nav{position:absolute;top:57px;left:319px;display:flex;gap:7px}
.nav-select{width:97px;height:25px;background:#fff;border:1px solid #ddd;font-size:11px;padding:0 10px;display:flex;align-items:center;justify-content:space-between}
.nav-select::after{content:"";border:5px solid transparent;border-top:6px solid #aaa;margin-top:5px}
.trending{position:absolute;left:740px;top:63px;font-size:11px;color:#777;white-space:nowrap}
.recipes{position:absolute;left:110px;top:101px;display:grid;grid-template-columns:repeat(4,164px);column-gap:14.4px;row-gap:16px}
.recipe{position:relative;width:164px;height:222px;background:#fff;box-shadow:0 1px 3px rgba(0,0,0,.5)}
.recipe-body{position:absolute;left:0;top:0;width:164px;height:195px;background:var(--card-bg);border:8px solid #fff;border-bottom:none}
.photo{position:absolute;left:8px;top:8px;width:148px;height:89px}
.p1{background:linear-gradient(135deg,#3a2a10,#b67a1c 50%,#e8b64a)}
.p2{background:linear-gradient(135deg,#d8a040,#a35416 55%,#3a1c08)}
.p3{background:linear-gradient(135deg,#edebe6,#c28538 55%,#6e3a10)}
.p4{background:linear-gradient(135deg,#8a9a30,#c9b058 55%,#5a4a10)}
.photo-title{position:absolute;left:8px;top:69px;width:148px;height:28px;background:rgba(20,15,10,.55);color:#fff;font-size:11px;text-align:center;line-height:28px;white-space:nowrap}
.meta{position:absolute;left:8px;top:106px;display:flex;gap:3px}
.meta-item{width:16px;height:26px;background:#ddd;text-align:center;font-size:8px;color:#555;padding-top:2px}
.meta-item svg{display:block;margin:0 auto 1px;width:10px;height:10px;fill:#999}
.type{position:absolute;right:-2px;top:102px;height:14px;padding:0 4px 0 14px;color:#fff;font-size:9px;line-height:14px;white-space:nowrap;clip-path:polygon(0 0,100% 0,100% 100%,0 100%,8px 50%)}
.extract{background:var(--red)} .partialmash{background:var(--orange)} .allgrain{background:var(--cyan)}
.style{position:absolute;right:8px;top:117px;width:68px;height:14px;background:#e0e0e0;font-size:9px;color:#888;text-align:right;padding-right:2px;line-height:14px;white-space:nowrap;clip-path:polygon(8px 0,100% 0,100% 100%,0 100%)}
.desc{position:absolute;left:9px;top:141px;width:148px;font-size:9.6px;line-height:13px}
.author{position:absolute;left:9px;top:172px;font-size:9.6px;color:#888;white-space:nowrap}
.author span{color:var(--author)}
.stats{position:absolute;left:1px;top:195px;width:162px;height:26px;display:flex;background:var(--stat-bg)}
.stat{flex:1;text-align:center;font-size:9px;line-height:11px;padding-top:2px;color:#333;border-right:1px solid #fff}
.stat:last-child{border:none;color:#fff}
.srm-red{background:var(--srm-red)} .srm-teal{background:var(--srm-teal)} .srm-green{background:var(--srm-green)} .srm-blue{background:var(--srm-blue)}
.footer-brand{position:absolute;left:370px;top:1078px;width:180px;height:40px;background:var(--cream);border-radius:50% 50% 0 0/100% 100% 0 0;display:flex;align-items:center;justify-content:center;gap:6px;font-size:18px;font-weight:700;color:var(--red);white-space:nowrap;padding-top:6px}
.footer-brand i{width:12px;height:12px;border-radius:50%;background:var(--red)}
.glasses{position:absolute;left:697px;top:1048px;width:108px;height:80px;border-radius:8px;background:radial-gradient(ellipse at 50% 60%,#c46c1c,#7a3a10 60%,rgba(80,40,10,0) 75%)}
.wood-edge{position:absolute;left:0;top:1110px;width:919px;height:10px;background:var(--wood-dark)}
.site-footer{position:absolute;left:0;top:1120px;width:919px;height:80px;background:var(--cream)}
.mailing{position:absolute;left:115px;top:13px;width:688px;height:37px;background:#fff;white-space:nowrap}
.mailing > *{position:absolute}
.mailing h2{left:6px;top:6px;font-family:Oswald,sans-serif;font-weight:500;font-size:17px;line-height:24px;color:var(--red);letter-spacing:.2px}
.mailing p{left:168px;top:12px;font-size:10px;line-height:13px}
.email{left:378px;top:8px;width:127px;height:20px;border:1px solid #ccc;border-right:none;border-radius:10px 0 0 10px;font-size:9.5px;color:#555;padding:3px 10px}
.join{left:505px;top:8px;width:27px;height:20px;background:var(--join);color:#fff;font-size:8.5px;font-weight:700;text-align:center;line-height:20px;border-radius:0 10px 10px 0}
.connect{left:535px;top:12px;font-style:italic;font-weight:800;font-size:9.5px;line-height:13px}
.social-foot{left:620px;top:9px;display:flex;gap:4px}
.social-foot i{width:18px;height:18px;background:var(--social)}
.copyright{position:absolute;left:0;top:60px;width:919px;text-align:center;font-size:10px;color:var(--copyright)}
</style>
</head>
<body>
<svg width="0" height="0" style="position:absolute">
  <symbol id="i-heart" viewBox="0 0 10 10"><path d="M5 9L1 5A2.2 2.2 0 0 1 5 2A2.2 2.2 0 0 1 9 5Z"/></symbol>
  <symbol id="i-thumbs" viewBox="0 0 10 10"><path d="M1 1h3v5H1zM4.5 1h4l1 4H7l.5 3-1 1L4.5 6z"/></symbol>
  <symbol id="i-star" viewBox="0 0 10 10"><path d="M5 .5l1.3 3 3.2.3-2.4 2.1.7 3.1L5 7.4 2.2 9l.7-3.1L.5 3.8l3.2-.3z"/></symbol>
  <symbol id="i-search" viewBox="0 0 10 10"><circle cx="4" cy="4" r="3" fill="none" stroke="#222" stroke-width="1.5"/><path d="M6 6l3 3" stroke="#222" stroke-width="1.8"/></symbol>
</svg>

<header class="site-header">
  <div class="brand"><span class="brand-dot"></span>Velvetfinch</div>
  <div class="search"><span>Search</span><b><svg width="10" height="10"><use href="#i-search"/></svg></b></div>
  <nav class="top-links"><span>Recipes</span><span>About ▾</span><span>Login</span></nav>
  <p class="tagline">Velvetfinch is the easiest way to create and share craft beer recipes.</p>
  <div class="share"><span>Like | 0</span><span>Send</span></div>
  <div class="social-top"><i></i><i></i></div>
  <div class="nav"><div class="nav-select">Brewing</div><div class="nav-select">Styles</div></div>
  <div class="trending">› Trending ▾</div>
</header>

<main class="recipes">
<article class="recipe"><div class="recipe-body"></div><div class="photo p1" role="img" aria-label="Beer being poured into a glass"></div><div class="photo-title">Oak Bastard Sweet Mead</div><div class="meta"><div class="meta-item"><svg><use href="#i-heart"/></svg>10</div><div class="meta-item"><svg><use href="#i-thumbs"/></svg>7</div><div class="meta-item"><svg><use href="#i-star"/></svg>0</div></div><div class="type extract">Extract</div><div class="style">Belgian Tripel</div><p class="desc">Lorem ipsum dolor sit amet, consectetur adipisicing elit.</p><p class="author">Created by <span>Dana Whitlow</span></p><div class="stats"><div class="stat">2.24%<br>ABV</div><div class="stat">24<br>IBU</div><div class="stat">1.006<br>FG</div><div class="stat">1.022<br>OG</div><div class="stat srm-red">4<br>SRM</div></div></article>

<article class="recipe"><div class="recipe-body"></div><div class="photo p2" role="img" aria-label="Beer tap pouring in a dark bar"></div><div class="photo-title">Oak Bastard Sweet Mead</div><div class="meta"><div class="meta-item"><svg><use href="#i-heart"/></svg>8</div><div class="meta-item"><svg><use href="#i-thumbs"/></svg>15</div><div class="meta-item"><svg><use href="#i-star"/></svg>0</div></div><div class="type partialmash">PartialMash</div><div class="style">Mild</div><p class="desc">Lorem ipsum dolor sit amet, consectetur adipisicing elit.</p><p class="author">Created by <span>Dana Whitlow</span></p><div class="stats"><div class="stat">2.24%<br>ABV</div><div class="stat">24<br>IBU</div><div class="stat">1.006<br>FG</div><div class="stat">1.022<br>OG</div><div class="stat srm-teal">4<br>SRM</div></div></article>

<article class="recipe"><div class="recipe-body"></div><div class="photo p2" role="img" aria-label="Glasses of amber beer on a bar"></div><div class="photo-title">Oak Bastard Sweet Mead</div><div class="meta"><div class="meta-item"><svg><use href="#i-heart"/></svg>6</div><div class="meta-item"><svg><use href="#i-thumbs"/></svg>3</div><div class="meta-item"><svg><use href="#i-star"/></svg>0</div></div><div class="type allgrain">AllGrain</div><div class="style">Belgian Tripel</div><p class="desc">Lorem ipsum dolor sit amet, consectetur adipisicing elit.</p><p class="author">Created by <span>Dana Whitlow</span></p><div class="stats"><div class="stat">2.24%<br>ABV</div><div class="stat">24<br>IBU</div><div class="stat">1.006<br>FG</div><div class="stat">1.022<br>OG</div><div class="stat srm-green">4<br>SRM</div></div></article>

<article class="recipe"><div class="recipe-body"></div><div class="photo p3" role="img" aria-label="Frothy pint of beer"></div><div class="photo-title">Oak Bastard Sweet Mead</div><div class="meta"><div class="meta-item"><svg><use href="#i-heart"/></svg>2</div><div class="meta-item"><svg><use href="#i-thumbs"/></svg>9</div><div class="meta-item"><svg><use href="#i-star"/></svg>0</div></div><div class="type extract">Extract</div><div class="style">Belgian Tripel</div><p class="desc">Lorem ipsum dolor sit amet, consectetur adipisicing elit.</p><p class="author">Created by <span>Dana Whitlow</span></p><div class="stats"><div class="stat">2.24%<br>ABV</div><div class="stat">24<br>IBU</div><div class="stat">1.006<br>FG</div><div class="stat">1.022<br>OG</div><div class="stat srm-red">4<br>SRM</div></div></article>

<article class="recipe"><div class="recipe-body"></div><div class="photo p3" role="img" aria-label="Beer glasses beside a wooden barrel"></div><div class="photo-title">Oak Bastard Sweet Mead</div><div class="meta"><div class="meta-item"><svg><use href="#i-heart"/></svg>5</div><div class="meta-item"><svg><use href="#i-thumbs"/></svg>20</div><div class="meta-item"><svg><use href="#i-star"/></svg>0</div></div><div class="type allgrain">AllGrain</div><div class="style">Belgian Tripel</div><p class="desc">Lorem ipsum dolor sit amet, consectetur adipisicing elit.</p><p class="author">Created by <span>Dana Whitlow</span></p><div class="stats"><div class="stat">2.24%<br>ABV</div><div class="stat">24<br>IBU</div><div class="stat">1.006<br>FG</div><div class="stat">1.022<br>OG</div><div class="stat srm-blue">4<br>SRM</div></div></article>

<article class="recipe"><div class="recipe-body"></div><div class="photo p2" role="img" aria-label="Two glasses of beer with warm lights"></div><div class="photo-title">Oak Bastard Sweet Mead</div><div class="meta"><div class="meta-item"><svg><use href="#i-heart"/></svg>0</div><div class="meta-item"><svg><use href="#i-thumbs"/></svg>6</div><div class="meta-item"><svg><use href="#i-star"/></svg>0</div></div><div class="type extract">Extract</div><div class="style">Munich Helles</div><p class="desc">Lorem ipsum dolor sit amet, consectetur adipisicing elit.</p><p class="author">Created by <span>Dana Whitlow</span></p><div class="stats"><div class="stat">2.24%<br>ABV</div><div class="stat">24<br>IBU</div><div class="stat">1.006<br>FG</div><div class="stat">1.022<br>OG</div><div class="stat srm-red">4<br>SRM</div></div></article>

<article class="recipe"><div class="recipe-body"></div><div class="photo p4" role="img" aria-label="Beer pouring from a can"></div><div class="photo-title">Oak Bastard Sweet Mead</div><div class="meta"><div class="meta-item"><svg><use href="#i-heart"/></svg>3</div><div class="meta-item"><svg><use href="#i-thumbs"/></svg>8</div><div class="meta-item"><svg><use href="#i-star"/></svg>0</div></div><div class="type partialmash">PartialMash</div><div class="style">Mild</div><p class="desc">Lorem ipsum dolor sit amet, consectetur adipisicing elit.</p><p class="author">Created by <span>Dana Whitlow</span></p><div class="stats"><div class="stat">2.24%<br>ABV</div><div class="stat">24<br>IBU</div><div class="stat">1.006<br>FG</div><div class="stat">1.022<br>OG</div><div class="stat srm-teal">4<br>SRM</div></div></article>

<article class="recipe"><div class="recipe-body"></div><div class="photo p1" role="img" aria-label="Mugs of beer with hops"></div><div class="photo-title">Oak Bastard Sweet Mead</div><div class="meta"><div class="meta-item"><svg><use href="#i-heart"/></svg>2</div><div class="meta-item"><svg><use href="#i-thumbs"/></svg>10</div><div class="meta-item"><svg><use href="#i-star"/></svg>0</div></div><div class="type allgrain">AllGrain</div><div class="style">Belgian Tripel</div><p class="desc">Lorem ipsum dolor sit amet, consectetur adipisicing elit.</p><p class="author">Created by <span>Dana Whitlow</span></p><div class="stats"><div class="stat">2.24%<br>ABV</div><div class="stat">24<br>IBU</div><div class="stat">1.006<br>FG</div><div class="stat">1.022<br>OG</div><div class="stat srm-green">4<br>SRM</div></div></article>

<article class="recipe"><div class="recipe-body"></div><div class="photo p3" role="img" aria-label="Close view of a foamy beer"></div><div class="photo-title">Oak Bastard Sweet Mead</div><div class="meta"><div class="meta-item"><svg><use href="#i-heart"/></svg>6</div><div class="meta-item"><svg><use href="#i-thumbs"/></svg>9</div><div class="meta-item"><svg><use href="#i-star"/></svg>0</div></div><div class="type partialmash">PartialMash</div><div class="style">Mild</div><p class="desc">Lorem ipsum dolor sit amet, consectetur adipisicing elit.</p><p class="author">Created by <span>Dana Whitlow</span></p><div class="stats"><div class="stat">2.24%<br>ABV</div><div class="stat">24<br>IBU</div><div class="stat">1.006<br>FG</div><div class="stat">1.022<br>OG</div><div class="stat srm-teal">4<br>SRM</div></div></article>

<article class="recipe"><div class="recipe-body"></div><div class="photo p1" role="img" aria-label="Cold glass of lager"></div><div class="photo-title">Oak Bastard Sweet Mead</div><div class="meta"><div class="meta-item"><svg><use href="#i-heart"/></svg>5</div><div class="meta-item"><svg><use href="#i-thumbs"/></svg>7</div><div class="meta-item"><svg><use href="#i-star"/></svg>0</div></div><div class="type allgrain">AllGrain</div><div class="style">English Cider</div><p class="desc">Lorem ipsum dolor sit amet, consectetur adipisicing elit.</p><p class="author">Created by <span>Dana Whitlow</span></p><div class="stats"><div class="stat">2.24%<br>ABV</div><div class="stat">24<br>IBU</div><div class="stat">1.006<br>FG</div><div class="stat">1.022<br>OG</div><div class="stat srm-blue">4<br>SRM</div></div></article>

<article class="recipe"><div class="recipe-body"></div><div class="photo p2" role="img" aria-label="Two glasses of beer with warm lights"></div><div class="photo-title">Oak Bastard Sweet Mead</div><div class="meta"><div class="meta-item"><svg><use href="#i-heart"/></svg>4</div><div class="meta-item"><svg><use href="#i-thumbs"/></svg>3</div><div class="meta-item"><svg><use href="#i-star"/></svg>0</div></div><div class="type extract">Extract</div><div class="style">Belgian Tripel</div><p class="desc">Lorem ipsum dolor sit amet, consectetur adipisicing elit.</p><p class="author">Created by <span>Dana Whitlow</span></p><div class="stats"><div class="stat">2.24%<br>ABV</div><div class="stat">24<br>IBU</div><div class="stat">1.006<br>FG</div><div class="stat">1.022<br>OG</div><div class="stat srm-green">4<br>SRM</div></div></article>

<article class="recipe"><div class="recipe-body"></div><div class="photo p2" role="img" aria-label="Glasses of amber beer on a bar"></div><div class="photo-title">Oak Bastard Sweet Mead</div><div class="meta"><div class="meta-item"><svg><use href="#i-heart"/></svg>3</div><div class="meta-item"><svg><use href="#i-thumbs"/></svg>11</div><div class="meta-item"><svg><use href="#i-star"/></svg>0</div></div><div class="type extract">Extract</div><div class="style">Belgian Tripel</div><p class="desc">Lorem ipsum dolor sit amet, consectetur adipisicing elit.</p><p class="author">Created by <span>Dana Whitlow</span></p><div class="stats"><div class="stat">2.24%<br>ABV</div><div class="stat">24<br>IBU</div><div class="stat">1.006<br>FG</div><div class="stat">1.022<br>OG</div><div class="stat srm-red">4<br>SRM</div></div></article>

<article class="recipe"><div class="recipe-body"></div><div class="photo p4" role="img" aria-label="Colourful cocktails and beer"></div><div class="photo-title">Oak Bastard Sweet Mead</div><div class="meta"><div class="meta-item"><svg><use href="#i-heart"/></svg>8</div><div class="meta-item"><svg><use href="#i-thumbs"/></svg>14</div><div class="meta-item"><svg><use href="#i-star"/></svg>0</div></div><div class="type extract">Extract</div><div class="style">Mild</div><p class="desc">Lorem ipsum dolor sit amet, consectetur adipisicing elit.</p><p class="author">Created by <span>Dana Whitlow</span></p><div class="stats"><div class="stat">2.24%<br>ABV</div><div class="stat">24<br>IBU</div><div class="stat">1.006<br>FG</div><div class="stat">1.022<br>OG</div><div class="stat srm-teal">4<br>SRM</div></div></article>

<article class="recipe"><div class="recipe-body"></div><div class="photo p2" role="img" aria-label="Beer being poured close up"></div><div class="photo-title">Oak Bastard Sweet Mead</div><div class="meta"><div class="meta-item"><svg><use href="#i-heart"/></svg>7</div><div class="meta-item"><svg><use href="#i-thumbs"/></svg>50</div><div class="meta-item"><svg><use href="#i-star"/></svg>0</div></div><div class="type extract">Extract</div><div class="style">Belgian Tripel</div><p class="desc">Lorem ipsum dolor sit amet, consectetur adipisicing elit.</p><p class="author">Created by <span>Dana Whitlow</span></p><div class="stats"><div class="stat">2.24%<br>ABV</div><div class="stat">24<br>IBU</div><div class="stat">1.006<br>FG</div><div class="stat">1.022<br>OG</div><div class="stat srm-green">4<br>SRM</div></div></article>

<article class="recipe"><div class="recipe-body"></div><div class="photo p3" role="img" aria-label="Beer glasses beside a wooden barrel"></div><div class="photo-title">Oak Bastard Sweet Mead</div><div class="meta"><div class="meta-item"><svg><use href="#i-heart"/></svg>4</div><div class="meta-item"><svg><use href="#i-thumbs"/></svg>20</div><div class="meta-item"><svg><use href="#i-star"/></svg>0</div></div><div class="type allgrain">AllGrain</div><div class="style">English Cider</div><p class="desc">Lorem ipsum dolor sit amet, consectetur adipisicing elit.</p><p class="author">Created by <span>Dana Whitlow</span></p><div class="stats"><div class="stat">2.24%<br>ABV</div><div class="stat">24<br>IBU</div><div class="stat">1.006<br>FG</div><div class="stat">1.022<br>OG</div><div class="stat srm-blue">4<br>SRM</div></div></article>

<article class="recipe"><div class="recipe-body"></div><div class="photo p2" role="img" aria-label="Blurred glasses of beer in a pub"></div><div class="photo-title">Oak Bastard Sweet Mead</div><div class="meta"><div class="meta-item"><svg><use href="#i-heart"/></svg>2</div><div class="meta-item"><svg><use href="#i-thumbs"/></svg>8</div><div class="meta-item"><svg><use href="#i-star"/></svg>0</div></div><div class="type partialmash">PartialMash</div><div class="style">Belgian Tripel</div><p class="desc">Lorem ipsum dolor sit amet, consectetur adipisicing elit.</p><p class="author">Created by <span>Dana Whitlow</span></p><div class="stats"><div class="stat">2.24%<br>ABV</div><div class="stat">24<br>IBU</div><div class="stat">1.006<br>FG</div><div class="stat">1.022<br>OG</div><div class="stat srm-red">4<br>SRM</div></div></article>
</main>

<div class="footer-brand"><i></i>Velvetfinch</div>
<div class="glasses" role="img" aria-label="Group of beer mugs"></div>
<div class="wood-edge"></div>

<footer class="site-footer">
  <div class="mailing">
    <h2>JOIN OUR MAILING LIST</h2>
    <p>Sign up for our e-mail list to receive updates</p>
    <div class="email">Your e-mail address</div>
    <div class="join">JOIN</div>
    <span class="connect">Connect with us on</span>
    <div class="social-foot"><i></i><i></i><i></i></div>
  </div>
  <p class="copyright">Copyright © 2013 Velvetfinch. All rights reserved.</p>
</footer>
</body>
</html>
```